Brookvane Consulting Business Card Design

Business Card Design for Brookvane Consulting. Brookvane Consulting is a boutique consultancy based in Atlanta, GA., that specializes in marketing strategy, organization planning, and leadership development. We provide solutions for small businesses and startups as well as Vantage 300 companies.

http://brookvaneconsulting.com/

Target Market(s)

We provide solutions for small businesses and startups as well as Vantage 300 companies.

Industry/Entity Type

Consulting

Contact Information for Business Card

Two sided business card with priority on contact information, logo, tag line (Inspiration to Dream More, Do More, Become More)

Colors

Designer to choose colors to be used in the design.

Requirements
Must have
• contact information, logo, tag line (Inspiration to Dream More, Do More, Become More)
• Simple no over communication.
Nice to have
• I would like to see different placements of logo and creative use of both sides of the card
Should not have
• Do not put too much information on the card.

```html
<!DOCTYPE html>
<html lang="en">
<head>
<meta charset="utf-8">
<title>Brookvane Consulting Business Card</title>
<link href="https://fonts.googleapis.com/css2?family=Quicksand:wght@300;500&family=Oswald:wght@500&family=Lato:ital,wght@0,400;1,700&display=swap" rel="stylesheet">
<style>
  :root {
    --backdrop: #e4e4e4;
    --card: #1d1d1f;
    --ink: #ececec;
    --ink-soft: #d6d6d6;
    --icon: #bdbdbd;
  }
  * { margin: 0; padding: 0; box-sizing: border-box; }
  html, body { width: 1200px; height: 960px; overflow: hidden; }
  body { background: var(--backdrop); position: relative; font-family: "Lato", sans-serif; }

  .card {
    position: absolute;
    width: 600px;
    height: 343px;
    background: var(--card);
    box-shadow: 2px 3px 5px rgba(0,0,0,0.35);
    color: var(--ink);
  }
  .card--front { left: 302px; top: 129px; }
  .card--back  { left: 299px; top: 488px; }

  .holder { position: absolute; right: 54px; top: 38px; text-align: right; }
  .holder__name {
    font-family: "Quicksand", sans-serif;
    font-weight: 300;
    font-size: 46px;
    line-height: 1;
    letter-spacing: -0.5px;
    color: var(--ink-soft);
  }
  .holder__role {
    font-family: "Oswald", sans-serif;
    font-weight: 500;
    font-size: 10.5px;
    letter-spacing: 0.4px;
    margin-top: 0;
    margin-right: 114px;
    color: var(--ink);
  }

  .contact { position: absolute; left: 43px; top: 248px; list-style: none; }
  .contact__item {
    display: flex; align-items: center;
    font-size: 15px; line-height: 19px;
    color: var(--ink-soft);
  }
  .contact__icon { width: 13px; height: 13px; margin-right: 8px; fill: var(--icon); }

  .brand {
    position: absolute; left: 0; right: 0; top: 128px;
    display: flex; justify-content: center; align-items: center; gap: 14px;
  }
  .brand__mark { width: 22px; height: 22px; background: var(--ink); }
  .brand__name {
    font-family: "Quicksand", sans-serif;
    font-weight: 500;
    font-size: 38px;
    letter-spacing: 0.5px;
    color: var(--ink);
  }

  .tagline {
    position: absolute; left: 0; right: 0; top: 273px;
    text-align: center;
    font-style: italic; font-weight: 700;
    font-size: 15px; line-height: 18px;
    color: var(--ink);
  }
</style>
</head>
<body>
  <section class="card card--front">
    <div class="holder">
      <div class="holder__name">Darius Whitfield</div>
      <div class="holder__role">FOUNDER/MANAGING DIRECTOR</div>
    </div>
    <ul class="contact">
      <li class="contact__item">
        <svg class="contact__icon" viewBox="0 0 16 16"><path d="M3.5 1.5l2.5 0 1.2 3.2-1.7 1.2c.8 1.8 2.3 3.3 4.1 4.1l1.2-1.7 3.2 1.2v2.5c0 .8-.7 1.5-1.5 1.5C6.7 13.5 2 8.8 2 3c0-.8.7-1.5 1.5-1.5z"/></svg>
        404-555-0183
      </li>
      <li class="contact__item">
        <svg class="contact__icon" viewBox="0 0 16 16"><path d="M1 3.5h14v9H1z M1.5 4l6.5 5 6.5-5" fill="none" stroke="#bdbdbd" stroke-width="1.4"/><rect x="1" y="3.5" width="14" height="9" fill="#bdbdbd"/><path d="M1.5 4.2l6.5 4.8 6.5-4.8" fill="none" stroke="#1d1d1f" stroke-width="1.3"/></svg>
        darius@brookvaneconsulting.com
      </li>
      <li class="contact__item">
        <svg class="contact__icon" viewBox="0 0 16 16"><circle cx="8" cy="8" r="7"/><path d="M4 4.5c1.5 0 2 1 3 1s.5 1.5-.5 2-1 1.8-.2 2.8M10 3.5c-.5 1 .5 1.5 1.5 1.5M9.5 9c1 0 2 1 1.5 2.5" fill="none" stroke="#1d1d1f" stroke-width="1.2"/></svg>
        brookvaneconsulting.com
      </li>
    </ul>
  </section>

  <section class="card card--back">
    <div class="brand">
      <span class="brand__mark"></span>
      <span class="brand__name">Brookvane Consulting</span>
    </div>
    <p class="tagline">Inspiration to Dream More<br>Do More, Become More</p>
  </section>
</body>
</html>
```